Business Card Design

We are a commercial real estate brokerage in San Francisco, leasing office buildings downtown.
I would like a clean, elegant look. Simple but powerful .

Industry/Entity Type

Business

Contact Information for Business Card

Derek Holloway
lic# 07258143
415.555.0172
derek@velt-commercial.example
velt-commercial.example

```html
<!DOCTYPE html>
<html lang="en">
<head>
<meta charset="utf-8">
<title>Velt Commercial – Business Card</title>
<link rel="stylesheet" href="https://fonts.googleapis.com/css2?family=PT+Sans:ital,wght@0,400;0,700;1,400&display=swap">
<style>
  :root {
    --backdrop: #8f9092;
    --card: #e8e8eb;
    --panel: #5f7090;
    --panel-edge: #4a5874;
    --panel-text: #f2f4f8;
    --ink: #3a3b3e;
    --ink-soft: #2f3033;
  }
  * { box-sizing: border-box; margin: 0; padding: 0; }
  html, body {
    width: 1105px; height: 1200px; overflow: hidden;
    background: var(--backdrop);
    font-family: "PT Sans", "Helvetica Neue", Arial, sans-serif;
  }
  .canvas { position: relative; width: 1105px; height: 1200px; }
  .card {
    position: absolute; left: 182px; width: 746px; height: 427px;
    background: var(--card); overflow: hidden;
  }
  .card--front { top: 119px; }
  .card--back { top: 635px; }

  .contact-panel {
    position: absolute; left: 0; top: 0; width: 395px; height: 100%;
    background: var(--panel); border-right: 4px solid var(--panel-edge);
    color: var(--panel-text);
  }
  .agent-name {
    position: absolute; left: 46px; top: 100px;
    font-size: 27px; font-weight: 700; letter-spacing: 0.5px;
  }
  .agent-licence {
    position: absolute; left: 46px; top: 138px; font-size: 19px;
  }
  .contact-list { position: absolute; left: 46px; top: 235px; list-style: none; }
  .contact-list li {
    display: flex; align-items: center; gap: 11px;
    font-size: 19px; height: 29px;
  }
  .contact-list svg { width: 17px; height: 17px; flex: none; fill: var(--panel-text); }

  .brand {
    position: absolute; left: 399px; right: 0; top: 0; bottom: 0;
    display: flex; flex-direction: column; align-items: center; justify-content: center;
    color: var(--ink); font-weight: 700; line-height: 1;
  }
  .brand-mark { width: 18px; height: 18px; background: var(--panel); margin-bottom: 18px; }
  .brand-name { font-size: 62px; letter-spacing: 1px; }
  .brand-sub { font-size: 27px; letter-spacing: 0.5px; margin-top: 4px; }

  .back-brand {
    position: absolute; left: 0; right: 0; top: 120px; text-align: center;
    color: var(--ink); font-weight: 700; font-size: 54px; letter-spacing: 1px; line-height: 1;
  }
  .tagline {
    position: absolute; left: 0; right: 0; top: 319px; text-align: center;
    font-style: italic; font-size: 19px; line-height: 28px; color: var(--ink-soft);
  }
</style>
</head>
<body>
<main class="canvas">
  <section class="card card--front">
    <div class="contact-panel">
      <h1 class="agent-name">DEREK HOLLOWAY</h1>
      <p class="agent-licence">lic# 07258143</p>
      <ul class="contact-list">
        <li><svg viewBox="0 0 24 24" aria-hidden="true"><path d="M6.6 10.8a15.1 15.1 0 0 0 6.6 6.6l2.2-2.2a1 1 0 0 1 1-.25 11.4 11.4 0 0 0 3.6.57 1 1 0 0 1 1 1V20a1 1 0 0 1-1 1A17 17 0 0 1 3 4a1 1 0 0 1 1-1h3.5a1 1 0 0 1 1 1c0 1.25.2 2.45.57 3.57a1 1 0 0 1-.25 1z"/></svg>415.555.0172</li>
        <li><svg viewBox="0 0 24 24" aria-hidden="true"><path d="M2 5h20v14H2zm2 2v.5l8 5 8-5V7zm0 2.8V17h16V9.8l-8 5z"/></svg>derek@velt-commercial.example</li>
        <li><svg viewBox="0 0 24 24" aria-hidden="true"><path d="M12 2a10 10 0 1 0 0 20 10 10 0 0 0 0-20zm6.9 9h-3a15 15 0 0 0-1.4-6.1A8 8 0 0 1 18.9 11zM12 4c.9 1.2 1.8 3.6 1.9 7h-3.8c.1-3.4 1-5.8 1.9-7zM9.5 4.9A15 15 0 0 0 8.1 11h-3a8 8 0 0 1 4.4-6.1zM5.1 13h3a15 15 0 0 0 1.4 6.1A8 8 0 0 1 5.1 13zM12 20c-.9-1.2-1.8-3.6-1.9-7h3.8c-.1 3.4-1 5.8-1.9 7zm2.5-.9a15 15 0 0 0 1.4-6.1h3a8 8 0 0 1-4.4 6.1z"/></svg>velt-commercial.example</li>
      </ul>
    </div>
    <div class="brand">
      <div class="brand-mark"></div>
      <div class="brand-name">VELT</div>
      <div class="brand-sub">COMMERCIAL</div>
    </div>
  </section>

  <section class="card card--back">
    <div class="back-brand">VELT COMMERCIAL</div>
    <p class="tagline">commercial real estate brokerage in San Francisco<br>leasing office buildings downtown.</p>
  </section>
</main>
</body>
</html>
```